Classy, Elegant, Simple Business Card Design

Looking to have a classy, simple, and elegant design. Want a top notch designed business card. I really like the look of the new torvane credit card. I also like the design I attached. I am trying to reach 21-29 year old females for booking us for there wedding or event. We offer Disc Jockey Service, Photo Booth Rentals, and Uplighting .

Target Market(s)

21-28 year old females

Contact Information for Business Card

Has to have logo, website, email, and phone number

Font styles to use
Other font styles liked:
• open to font choice, modern, clean
Designer to choose
33a6d7
0791cd
0555a3
ffffff

Requirements
Must have
• Has to have logo, website, email, and phone number
Nice to have
• I really like the design of the new torvane credit card. I also included my logo and some designs I like
Should not have
• clutter or too much info

```html
<!DOCTYPE html>
<html lang="en">
<head>
<meta charset="utf-8">
<title>Corvessa Event Group – Business Card</title>
<link href="https://fonts.googleapis.com/css2?family=Jost:wght@400;500&family=Roboto:wght@400;700&display=swap" rel="stylesheet">
<style>
  :root {
    --sky: #33a6d7;
    --azure: #0791cd;
    --navy: #0555a3;
    --white: #ffffff;
    --ink: #2a3442;
    --muted: #8a929b;
    --backdrop: #e9e6e1;
    --card: #f1f3f4;
  }
  * { margin: 0; padding: 0; box-sizing: border-box; }
  html, body {
    width: 1200px;
    height: 1054px;
    overflow: hidden;
    background: var(--backdrop);
  }
  .business-card {
    position: absolute;
    left: 172px;
    top: 293px;
    width: 857px;
    height: 516px;
    background: var(--card);
    border: 1px solid var(--white);
    box-shadow: 0 10px 30px rgba(0,0,0,0.12);
  }
  .brand {
    position: absolute;
    left: 53px;
    top: 58px;
  }
  .brand-name {
    font-family: "Jost", sans-serif;
    font-weight: 500;
    font-size: 37px;
    letter-spacing: 1px;
    line-height: 1;
    color: var(--navy);
  }
  .brand-tagline {
    margin-top: 5px;
    font-family: "Jost", sans-serif;
    font-weight: 400;
    font-size: 16px;
    letter-spacing: 9px;
    line-height: 1;
    color: var(--muted);
    text-align: center;
    padding-left: 9px;
  }
  .person {
    position: absolute;
    left: 53px;
    top: 279px;
    font-family: "Roboto", sans-serif;
  }
  .person-name {
    font-weight: 700;
    font-size: 32px;
    line-height: 1.1;
    color: var(--navy);
  }
  .person-title {
    margin-top: 5px;
    font-weight: 400;
    font-size: 19px;
    color: var(--ink);
  }
  .contact-list {
    position: absolute;
    left: 53px;
    top: 375px;
    list-style: none;
    font-family: "Roboto", sans-serif;
    font-size: 20px;
    color: var(--ink);
  }
  .contact-item {
    display: flex;
    align-items: center;
    height: 33px;
  }
  .contact-icon {
    width: 19px;
    height: 19px;
    margin-right: 20px;
    fill: var(--navy);
  }
  .logo-mark-area {
    position: absolute;
    left: 493px;
    top: 53px;
    width: 319px;
    height: 415px;
    border-radius: 12px;
    background: radial-gradient(ellipse at 50% 50%, rgba(51,166,215,0.35), rgba(7,145,205,0.12) 60%, rgba(241,243,244,0) 80%);
  }
</style>
</head>
<body>
  <main class="business-card">
    <header class="brand">
      <div class="brand-name">CORVESSA</div>
      <div class="brand-tagline">EVENT GROUP</div>
    </header>

    <section class="person">
      <div class="person-name">Daniel Marsh</div>
      <div class="person-title">Founder &amp; CEO</div>
    </section>

    <ul class="contact-list">
      <li class="contact-item">
        <svg class="contact-icon" viewBox="0 0 24 24" aria-hidden="true">
          <path d="M3 7c0-2 2-3 9-3s9 1 9 3v2h-5V7H8v2H3z"/>
          <path d="M6 11h12l2 9H4z"/>
        </svg>
        <span>555 0142 0142</span>
      </li>
      <li class="contact-item">
        <svg class="contact-icon" viewBox="0 0 24 24" aria-hidden="true">
          <path d="M2 5h20v14H2z M4 7v1l8 5 8-5V7l-8 5z" fill-rule="evenodd"/>
        </svg>
        <span>daniel@corvessa.com</span>
      </li>
      <li class="contact-item">
        <svg class="contact-icon" viewBox="0 0 24 24" aria-hidden="true">
          <circle cx="12" cy="12" r="10"/>
          <path d="M2 12h20 M12 2c-4 4-4 16 0 20 M12 2c4 4 4 16 0 20" stroke="#f1f3f4" stroke-width="1.5" fill="none"/>
        </svg>
        <span>www.corvessa.com</span>
      </li>
    </ul>

    <div class="logo-mark-area" role="img" aria-label="Large brand monogram in blue"></div>
  </main>
</body>
</html>
```